Refresh of far from plain IT company website

Our web site is starting to show it's age. You can see the existing site here: www.plumbwick.net. As a growing company we want to come across as a dynamic collection of IT experts.

We want to update the design so are open to any colour palette and look, but want to retain our current table logo. We use the logo on our business cards but with a white background - see the attached file, so you don't need to keep the brown or the green.

The design should consider the range of browsers that will be looking at the site - so please show how it will look on a wide screen laptop and a 768x1024 tablet.

We want to add some pages about our team and their skills, probably with photos of each person on the team.

This is an uncoded project - the PSD files of the design is required, not coding.
Updates

Thanks everyone for the submissions so far.  It's a holiday day in the UK today but we will get some feedback on the designs so far out to you.

Target Market(s)

Architects and other creative types looking for IT support

Industry/Entity Type

Business

Font styles to use
Serif
Sans Serif

Requirements
Must have
• Must look good on a laptop and an iPad.

```html
<!DOCTYPE html>
<html lang="en">
<head>
<meta charset="utf-8">
<title>plumbwick – IT support</title>
<link href="https://fonts.googleapis.com/css2?family=Open+Sans:ital,wght@0,400;0,600;0,700;1,400&family=Oswald:wght@400&display=swap" rel="stylesheet">
<style>
:root{
  --plum:#9e1456;
  --plum-dark:#7f0f45;
  --hero:#a5195b;
  --gold:#d2a512;
  --gold-dark:#a88208;
  --ink:#333;
  --muted:#555;
  --line:#dcdcdc;
  --page:#f3f3f3;
  --footer:#383838;
  --footer-dark:#2a2a2a;
  --footer-text:#eee;
}
*{margin:0;padding:0;box-sizing:border-box}
html,body{width:1200px;height:2326px;overflow:hidden}
body{position:relative;background:var(--page);font-family:"Open Sans",Arial,sans-serif;color:var(--ink)}
.abs{position:absolute}

/* header */
.site-header{left:0;top:0;width:1200px;height:115px;background:#f8f8f8}
.brand{left:132px;top:44px;display:flex;align-items:center;gap:12px}
.brand-mark{width:28px;height:28px;background:var(--gold)}
.brand-name{font-size:29px;font-weight:600;color:var(--plum)}
.main-nav{left:431px;top:0;display:flex;height:115px}
.main-nav a{display:flex;align-items:center;padding:0 12px;font-size:13px;color:#333;text-decoration:none;text-transform:uppercase;border-right:1px solid #e2e2e2}
.main-nav a:last-child{border-right:0}
.main-nav a.active{background:#e9e9e9;color:var(--plum);padding:0 19px}

/* hero */
.hero{left:0;top:115px;width:1200px;height:466px;background:var(--hero)}
.hero-lines{left:132px;top:203px}
.hero-lines span{display:table;background:var(--gold);color:#fff;font-family:"Oswald",Arial,sans-serif;font-size:29px;line-height:43px;padding:0 12px;margin-bottom:6px;text-transform:uppercase}
.hero-devices{left:546px;top:180px;width:466px;height:280px;border-radius:10px;background:linear-gradient(135deg,#2b2b2b 0%,#4a5a6a 45%,#e6e6e6 100%)}

/* panel */
.panel{left:132px;top:493px;width:936px;height:1465px;background:#fff;border-top:4px solid var(--gold);box-shadow:0 0 6px rgba(0,0,0,.06)}
.bookmark{left:575px;top:493px}
.pointer{left:578px;top:1957px}
.welcome{left:132px;top:562px;width:936px;text-align:center;font-size:30px;font-weight:400;color:var(--gold);display:flex;justify-content:center;align-items:center;gap:12px}
.welcome .name{color:var(--plum)}
.welcome .mark{width:26px;height:26px;background:var(--gold)}
.intro{left:160px;top:617px;width:880px;text-align:center;font-size:15.5px;line-height:24px;color:var(--muted)}

.section-rule{left:140px;width:920px;height:1px;background:var(--line)}
.ribbon{height:42px;background:var(--gold);color:#fff;font-size:19px;display:flex;align-items:center;justify-content:center;clip-path:polygon(14px 0,calc(100% - 14px) 0,100% 50%,calc(100% - 14px) 100%,14px 100%,0 50%)}

.service{width:200px;text-align:center}
.service .disc{width:112px;height:112px;border-radius:50%;background:var(--plum-dark);margin:0 auto;display:flex;align-items:center;justify-content:center}
.service h3{margin-top:22px;font-size:15.5px;font-weight:700;letter-spacing:.3px;color:#222}
.soft-rule{left:150px;width:900px;height:14px;background:radial-gradient(ellipse at top,rgba(0,0,0,.08),rgba(0,0,0,0) 70%)}

.ticks{list-style:none;width:400px;font-size:13px;line-height:19px;color:var(--muted)}
.ticks li{position:relative;padding-left:28px;margin-bottom:18px}
.ticks svg{position:absolute;left:0;top:2px}
.btn{left:927px;top:1180px;width:110px;height:31px;background:var(--plum);color:#fff;font-size:14px;border-radius:3px;display:flex;align-items:center;justify-content:center;gap:8px}

.lead{left:160px;top:1302px;width:880px;text-align:center;font-size:16px;line-height:28px;color:var(--muted)}
.small{left:170px;top:1366px;width:860px;text-align:center;font-size:11.5px;line-height:21px;color:var(--muted)}

.card{top:1441px;width:188px;height:235px;background:#fff;border:1px solid #ddd;box-shadow:0 1px 3px rgba(0,0,0,.12);padding:10px 11px}
.card .photo{height:124px}
.card .bar{height:2px;background:var(--gold);margin:10px 0 8px}
.card h4{font-size:12px;font-weight:700;color:var(--plum)}
.card p{font-size:11.5px;line-height:16px;color:#666;margin-top:4px}
.card .more{font-size:11px;color:#333;margin-top:5px;display:flex;gap:10px;align-items:center}
.arrow{top:1538px}

.avatar{left:154px;top:1805px;width:86px;height:86px;border-radius:50%;border:3px solid var(--gold);background:linear-gradient(#d6dbe0,#8a96a3)}
.quote{left:279px;top:1810px;width:760px;font-size:11.5px;line-height:21px;font-style:italic;color:#666;text-indent:14px}
.quote-mark{left:264px;top:1796px;font-size:34px;color:#ccc;font-family:Georgia,serif}
.quote-rule{left:279px;top:1882px;width:760px;height:1px;background:var(--line)}
.author{left:286px;top:1893px;font-size:13px;font-weight:700;color:#333}
.dots{left:968px;top:1902px;display:flex;gap:6px}
.dots i{width:9px;height:9px;border-radius:50%;background:#ddd}
.dots i:first-child{background:var(--gold)}

/* footer */
.site-footer{left:0;top:2040px;width:1200px;height:250px;background:var(--footer)}
.notch{left:578px;top:2040px}
.foot-col{top:2083px;color:var(--footer-text)}
.foot-col h5{font-size:15.5px;font-weight:600;color:#fff;padding-bottom:7px;border-bottom:1px solid #777;display:inline-block;min-width:118px}
.quick{list-style:none;margin-top:8px;font-size:12px;line-height:24.5px}
.quick li::before{content:"";display:inline-block;border-left:5px solid #ddd;border-top:4px solid transparent;border-bottom:4px solid transparent;margin-right:10px}
.news p{font-size:12px;line-height:18px;margin-top:8px;width:215px}
.field{width:214px;height:24px;background:#fff;color:#333;font-size:12px;padding:4px 8px;margin-top:8px}
.sub{display:inline-block;background:var(--plum);color:#fff;font-size:12.5px;font-weight:600;padding:3px 12px;margin-top:10px}
.contact-row{display:flex;gap:16px;margin-top:13px;font-size:12px;line-height:18px}
.social{list-style:none;margin-top:2px}
.social li{display:flex;align-items:center;gap:20px;font-size:12px;height:39px}
.social b{width:28px;height:28px;background:#2f6db3;display:block}
.legal{left:0;top:2290px;width:1200px;height:36px;background:var(--footer-dark);color:#ccc;font-size:12px;display:flex;align-items:center;justify-content:center}
</style>
</head>
<body>

<header class="abs site-header">
  <div class="abs brand"><span class="brand-mark"></span><span class="brand-name">plumbwick</span></div>
  <nav class="abs main-nav">
    <a class="active">About Us</a><a>What We Do</a><a>News Blog</a><a>Articles</a><a>Clients</a><a>Partners</a><a>Contact</a>
  </nav>
</header>

<section class="abs hero"></section>
<div class="abs hero-lines">
  <span>Provides a high quality</span>
  <span>One-stop IT support</span>
  <span>Solution for your business</span>
</div>
<div class="abs hero-devices" role="img" aria-label="Desktop monitor and tablet displaying the plumbwick website"></div>

<main class="abs panel"></main>
<svg class="abs bookmark" width="50" height="44" viewBox="0 0 50 44"><polygon points="0,0 25,0 25,44 0,26" fill="var(--gold)"/><polygon points="25,0 50,0 50,26 25,44" fill="var(--plum-dark)"/></svg>

<h1 class="abs welcome"><span class="mark"></span><span>Welcome to <span class="name">plumbwick</span></span></h1>
<p class="abs intro">Lorem ipsum dolor sit amet, consectetur adipiscing elit. Curabitur quis velit nunc. Vivamus ac venenatis dui, eu placerat lacus. Donec at lorem et quam condimentum vestibulum. Praesent sed elit in quam volutpat faucibus. Aliquam eget ultrices elit, laoreet auctor metus. Curabitur nec lacus est. Suspendisse potenti. Vivamus suscipit massa commodo dolor blandit, nec et sem venenatis. Maecenas sed justo et orci tristique gravida adipiscing a dolor.</p>

<div class="abs section-rule" style="top:777px"></div>
<div class="abs ribbon" style="left:442px;top:756px;width:318px">WHY PEOPLE CHOOSE US</div>

<div class="abs service" style="left:162px;top:841px">
  <div class="disc"><svg width="56" height="50" viewBox="0 0 56 50"><path d="M8 12c3-3 6-3 8 0l4 6c1 2 0 4-2 5l-2 1c2 5 6 9 11 11l1-2c1-2 3-3 5-2l6 4c3 2 3 5 0 8-3 3-8 4-13 1C15 40 8 33 5 24 3 19 5 15 8 12z" fill="#fff"/><text x="34" y="14" fill="#fff" font-size="14" font-weight="700" font-family="Open Sans,sans-serif">24</text></svg></div>
  <h3>SUPPORT</h3>
</div>
<div class="abs service" style="left:379px;top:841px">
  <div class="disc"><svg width="48" height="40" viewBox="0 0 48 40"><circle cx="17" cy="11" r="7" fill="#fff"/><circle cx="32" cy="11" r="7" fill="#fff"/><path d="M3 34c0-8 6-13 14-13s14 5 14 13z" fill="#fff"/><path d="M24 23c2-1 5-2 8-2 8 0 13 5 13 13H34" fill="#fff"/></svg></div>
  <h3>CONSULTANCY</h3>
</div>
<div class="abs service" style="left:596px;top:841px">
  <div class="disc"><svg width="46" height="42" viewBox="0 0 46 42"><rect x="3" y="3" width="20" height="24" fill="none" stroke="#fff" stroke-width="3"/><line x1="8" y1="10" x2="18" y2="10" stroke="#fff" stroke-width="3"/><line x1="8" y1="16" x2="18" y2="16" stroke="#fff" stroke-width="3"/><rect x="20" y="19" width="22" height="14" fill="none" stroke="#fff" stroke-width="3"/><line x1="26" y1="38" x2="36" y2="38" stroke="#fff" stroke-width="3"/></svg></div>
  <h3>HOSTING</h3>
</div>
<div class="abs service" style="left:822px;top:841px">
  <div class="disc"><svg width="48" height="40" viewBox="0 0 48 40"><circle cx="24" cy="8" r="6" fill="#fff"/><circle cx="9" cy="16" r="5" fill="#fff"/><circle cx="39" cy="16" r="5" fill="#fff"/><path d="M14 34c0-8 4-13 10-13s10 5 10 13z" fill="#fff"/><path d="M1 34c0-6 3-10 8-10 2 0 4 1 5 2l-2 8zM47 34c0-6-3-10-8-10-2 0-4 1-5 2l2 8z" fill="#fff"/></svg></div>
  <h3>DEVELOPMENT</h3>
</div>

<div class="abs soft-rule" style="top:1026px"></div>

<ul class="abs ticks" style="left:158px;top:1061px">
  <li><svg width="16" height="14" viewBox="0 0 16 14"><path d="M1 7l5 5L15 1" fill="none" stroke="#2f8fbf" stroke-width="2"/></svg>Morbi et urna quis justo dapibus rhoncus vitae non est. Pellentesque.</li>
  <li><svg width="16" height="14" viewBox="0 0 16 14"><path d="M1 7l5 5L15 1" fill="none" stroke="#2f8fbf" stroke-width="2"/></svg>Curabitur non orci et leo vulputate porta et at est. Donec venenatis massa sed sodales bibendum.</li>
</ul>
<ul class="abs ticks" style="left:645px;top:1059px">
  <li><svg width="16" height="14" viewBox="0 0 16 14"><path d="M1 7l5 5L15 1" fill="none" stroke="#2f8fbf" stroke-width="2"/></svg>Fusce pharetra suscipit nisl, at blandit erat. Etiam innulla lectus. Vestibulum eleifend sit amet dui vel tempus.</li>
  <li><svg width="16" height="14" viewBox="0 0 16 14"><path d="M1 7l5 5L15 1" fill="none" stroke="#2f8fbf" stroke-width="2"/></svg>Quisque imperdiet felis odio, facilisis congue augue fringilla ut. Nulla sit amet mattis purus.</li>
</ul>
<div class="abs btn">Read More <svg width="12" height="8" viewBox="0 0 12 8"><path d="M0 4h10M7 1l3 3-3 3" stroke="#fff" fill="none" stroke-width="1.5"/></svg></div>

<div class="abs section-rule" style="top:1264px;left:148px;width:904px"></div>
<div class="abs ribbon" style="left:409px;top:1242px;width:394px">SUCCESSFUL COMPLETED PROJECTS</div>

<p class="abs lead">Lorem ipsum dolor sit amet, consectetuer adipiscing elit, sed diam nonummy nibh euismod tincidunt ut laoreet dolore magna aliquam erat volutpat. Ut wisi enim ad minim veniam, quis nostrud exerci tation ullamcorper</p>
<p class="abs small">Lorem ipsum dolor sit amet, consectetuer adipiscing elit, sed diam nonummy nibh euismod tincidunt ut laoreet dolore magna aliquam erat volutpat. Ut wisi enim ad minim veniam, quis nostrud exerci tation ullamcorper</p>

<svg class="abs arrow" style="left:147px" width="20" height="36" viewBox="0 0 20 36"><polygon points="18,0 18,36 0,18" fill="#ccc"/></svg>
<svg class="abs arrow" style="left:1043px" width="20" height="36" viewBox="0 0 20 36"><polygon points="2,0 2,36 20,18" fill="#ccc"/></svg>

<article class="abs card" style="left:186px">
  <div class="photo" role="img" aria-label="Engineers working in a server room" style="background:linear-gradient(#c9d2dc,#5b6b80)"></div>
  <div class="bar"></div><h4>Maecenas Sollicitudin</h4><p>Adipiscing elit, sed diams is a nonummy hi goold euismod</p>
  <div class="more">View More <svg width="10" height="8" viewBox="0 0 10 8"><path d="M0 4h8M5 1l3 3-3 3" stroke="#333" fill="none"/></svg></div>
</article>
<article class="abs card" style="left:403px">
  <div class="photo" role="img" aria-label="Businesswoman checking her phone in an office" style="background:linear-gradient(#e4e6e8,#9aa2aa)"></div>
  <div class="bar"></div><h4>Quisque Sit Amet</h4><p>Adipiscing elit, sed diams is a nonummy hi goold euismod</p>
  <div class="more">View More <svg width="10" height="8" viewBox="0 0 10 8"><path d="M0 4h8M5 1l3 3-3 3" stroke="#333" fill="none"/></svg></div>
</article>
<article class="abs card" style="left:620px">
  <div class="photo" role="img" aria-label="Hand pointing at charts on a tablet" style="background:linear-gradient(#f2f5f8,#9cc0dc)"></div>
  <div class="bar"></div><h4>Vulputate Neque Nec</h4><p>Adipiscing elit, sed diams is a nonummy hi goold euismod</p>
  <div class="more">View More <svg width="10" height="8" viewBox="0 0 10 8"><path d="M0 4h8M5 1l3 3-3 3" stroke="#333" fill="none"/></svg></div>
</article>
<article class="abs card" style="left:836px">
  <div class="photo" role="img" aria-label="Server tower in blue clouds" style="background:linear-gradient(#2d6fc4,#cfe3f6)"></div>
  <div class="bar"></div><h4>Malesuada Consectur</h4><p>Adipiscing elit, sed diams is a nonummy hi goold euismod</p>
  <div class="more">View More <svg width="10" height="8" viewBox="0 0 10 8"><path d="M0 4h8M5 1l3 3-3 3" stroke="#333" fill="none"/></svg></div>
</article>

<div class="abs soft-rule" style="top:1751px"></div>

<div class="abs avatar" role="img" aria-label="Portrait of client"></div>
<div class="abs quote-mark">“</div>
<p class="abs quote">Lorem ipsum dolor sit amet consectetur adipisicing elitsed do eiusmod tempor incididunt ut labore et dolore magna aliqua. Ut enim ad minim vesniam, quis nostrud exercitation ullamco laboris nisi ut aliquip ex ea commodo consequat. Duis aute irure dolor in reprehenderit in voluptate velit esse cillum is a dolore eu fugiat nulla pariatur. Excepteur sint occaecat cupidatat non proident, sunt in culpa qui officia deserunt mollit</p>
<div class="abs quote-rule"></div>
<div class="abs author">Mr. Dorian Vale</div>
<div class="abs dots"><i></i><i></i><i></i><i></i></div>
<svg class="abs pointer" width="44" height="26" viewBox="0 0 44 26"><polygon points="0,0 44,0 22,26" fill="#fff"/></svg>

<footer class="abs site-footer"></footer>
<svg class="abs notch" width="44" height="20" viewBox="0 0 44 20"><polygon points="0,0 44,0 22,20" fill="var(--page)"/></svg>

<div class="abs foot-col" style="left:132px">
  <h5>Quick Links</h5>
  <ul class="quick"><li>Home</li><li>About Us</li><li>What We Do</li><li>News Blog</li><li>Articals</li><li>Contact</li></ul>
</div>
<div class="abs foot-col news" style="left:346px">
  <h5 style="min-width:207px">Newsletter</h5>
  <p>Signup with us and get update in your inbox.</p>
  <div class="field">Your Name</div>
  <div class="field">Email address</div>
  <div class="sub">Subscribe</div>
</div>
<div class="abs foot-col" style="left:660px">
  <h5 style="min-width:197px">Contact Us</h5>
  <div class="contact-row"><svg width="14" height="20" viewBox="0 0 14 20"><path d="M7 0a7 7 0 0 1 7 7c0 5-7 13-7 13S0 12 0 7a7 7 0 0 1 7-7z" fill="#fff"/><circle cx="7" cy="7" r="2.5" fill="var(--footer)"/></svg><span>Lorem ipsum dolsi consectetuer<br>adipiscing elitUt wisi enim ad<br>ST 56 - 54</span></div>
  <div class="contact-row" style="font-size:15.5px;align-items:center"><svg width="12" height="18" viewBox="0 0 12 18"><rect x="1" y="1" width="10" height="16" rx="2" fill="none" stroke="#fff" stroke-width="2"/><rect x="4" y="13" width="4" height="2" fill="#fff"/></svg><span>0987 654 321</span></div>
  <div class="contact-row" style="align-items:center"><svg width="18" height="14" viewBox="0 0 18 14"><rect x="1" y="1" width="16" height="12" fill="none" stroke="#fff" stroke-width="2"/><path d="M1 1l8 7 8-7" fill="none" stroke="#fff" stroke-width="2"/></svg><span>info@plumbwick</span></div>
</div>
<div class="abs foot-col" style="left:959px">
  <h5 style="min-width:104px">Follow Us On</h5>
  <ul class="social"><li><b></b>Friendbook</li><li><b style="background:#3aa9e0"></b>Chirper</li><li><b style="background:#c8302a"></b>Tubecast</li><li><b style="background:#1a74b3"></b>Linkwork</li></ul>
</div>

<div class="abs legal">© 2014 plumbwick.com &nbsp;|&nbsp; All rights reserved</div>

</body>
</html>
```